Website Design for Hulls for Heroes

Please design and code a new website.
Here are the sites I like best:
http://www.sailbrisk.com/alternate/
http://www.wheelsforhonor.org
Please make it similar. This is NOT a car donation site. It's a boat donation site. I just like this sites above as a lead generation sites.
Old site:
http://hullsforheroes.org
Updates
Coding
Coded - Design and coding required
Number of Pages Required
1 page
Look and feel
Each slider illustrates characteristics of the customer's brand and the style your logo design should communicate.

```html
<!DOCTYPE html>
<html lang="en">
<head>
<meta charset="utf-8">
<title>Hulls for Heroes — Donate Your Boat</title>
<link rel="stylesheet" href="https://fonts.googleapis.com/css2?family=Open+Sans:wght@400;600;700;800&family=Roboto+Condensed:wght@700&display=swap">
<style>
:root{
  --navy:#0d2a6b;
  --navy-deep:#081b4a;
  --blue:#1a3f93;
  --red:#a3120f;
  --red-bright:#c0201b;
  --ink:#222831;
  --muted:#4a4f58;
  --white:#ffffff;
  --line:#d6d9de;
  --header-dark:#1d1f2b;
}
*{box-sizing:border-box;margin:0;padding:0}
html,body{width:1200px;height:2786px;overflow:hidden}
body{position:relative;font-family:"Open Sans",Arial,sans-serif;color:var(--ink);background:var(--white)}
.abs{position:absolute}

/* Header */
.site-header{left:0;top:0;width:1200px;height:160px;background:linear-gradient(100deg,#2a2c3a 0%,#4a3a44 40%,#1c2030 70%,#161a28 100%)}
.brand{left:214px;top:62px;font-family:"Roboto Condensed",Arial,sans-serif;font-size:34px;color:#e6c98a;letter-spacing:.5px;display:flex;align-items:center;gap:14px}
.brand-dot{width:14px;height:14px;border-radius:50%;background:#e6c98a}
.call-box{display:flex;align-items:center;gap:14px;color:var(--white)}
.call-box .ring{width:72px;height:72px;border:3px solid var(--white);border-radius:50%;display:flex;align-items:center;justify-content:center}
.call-box .label{font-family:"Roboto Condensed",Arial,sans-serif;font-size:22px;line-height:1}
.call-box .number{font-family:"Roboto Condensed",Arial,sans-serif;font-size:37px;line-height:1.05}
.call-box .note{font-size:13px;font-weight:700}
.header-call{left:800px;top:22px}

/* Nav */
.main-nav{left:0;top:160px;width:808px;height:40px;background:var(--navy);display:flex;align-items:center}
.main-nav a{position:absolute;color:var(--white);text-decoration:none;font-weight:700;font-size:15px}

/* Hero */
.hero-photo{left:0;top:200px;width:808px;height:490px;background:linear-gradient(160deg,#dfe8ee 0%,#c9d4da 45%,#8c8f7c 75%,#6f6f5f 100%)}

/* Donation form */
.donate-form{left:808px;top:130px;width:352px;height:560px;background:var(--red);padding:0 20px;color:var(--white)}
.donate-form .form-icon{margin:14px auto 0;width:24px;height:24px;border:3px solid var(--white);border-radius:50%}
.donate-form h2{text-align:center;font-size:19px;font-weight:800;margin-top:4px;line-height:1.2}
.donate-form .sub{margin:18px -20px 0;padding:9px 0;text-align:center;font-size:15px;font-weight:700;background:#8e0f0c}
.fields{display:grid;grid-template-columns:1fr 1fr;gap:11px 10px;margin-top:10px}
.field{height:32px;background:var(--white);color:#8e1b18;font-size:13px;font-weight:600;padding:0 10px;display:flex;align-items:center;justify-content:space-between;border-radius:2px}
.field.wide{grid-column:span 2}
.field .caret{width:0;height:0;border-left:6px solid transparent;border-right:6px solid transparent;border-top:7px solid #8e1b18}
.btn-donate{margin-top:14px;width:155px;height:40px;background:var(--navy);color:var(--white);font-weight:800;font-size:15px;display:flex;align-items:center;justify-content:center;border-radius:3px}

/* Benefit band */
.benefit-band{left:0;top:690px;width:1200px;height:202px;background:linear-gradient(90deg,#24438f 0%,#1e3c86 50%,#2a4a9a 100%)}
.band-badge{left:0;top:668px;width:520px;height:226px}
.band-badge-text{left:120px;top:722px;text-align:center;color:var(--white);font-weight:800}
.band-badge-text .l1{font-size:27px}
.band-badge-text .l2{font-family:"Roboto Condensed",Arial,sans-serif;font-size:64px;line-height:1;color:#d9d9de;letter-spacing:2px}
.band-badge-text .l3{font-size:29px}
.perk{width:130px;text-align:center;color:var(--white);font-family:"Roboto Condensed",Arial,sans-serif;font-size:16px;line-height:1.15;top:735px}
.perk svg{display:block;margin:0 auto 12px}

/* Section titles */
.section-title{left:0;width:1200px;text-align:center;font-size:29px;font-weight:800;color:var(--navy);display:flex;align-items:center;justify-content:center;gap:22px}
.section-title::before,.section-title::after{content:"";width:95px;height:1px;background:#9aa0aa}
.section-title em{font-style:normal;color:var(--red)}

/* How to donate */
.step{width:330px;display:flex;gap:20px;top:1050px}
.step h3{font-size:14px;font-weight:800;color:var(--navy);text-transform:uppercase;line-height:1.25;margin-top:18px}
.step p{font-size:13.5px;font-weight:600;color:var(--muted);line-height:1.45;margin-top:10px}
.step .icon{flex:0 0 70px}

/* Why donate */
.why-band{left:0;top:1262px;width:1200px;height:412px;background:linear-gradient(180deg,#eceef0 0%,#dfe2e5 50%,#e9ebed 100%)}
.reason{width:350px;display:flex;gap:18px}
.reason .disc{flex:0 0 64px;height:64px;border-radius:50%;display:flex;align-items:center;justify-content:center}
.disc.navy{background:var(--navy)}
.disc.red{background:var(--red)}
.reason p{font-size:14.5px;line-height:1.35;color:var(--ink)}
.reason b{font-weight:700}

/* FAQ */
.faq{left:74px;top:1806px;width:492px}
.faq-item{border:1px solid var(--line);border-radius:6px;padding:0 16px;margin-bottom:10px;box-shadow:0 1px 2px rgba(0,0,0,.06)}
.faq-q{height:38px;display:flex;align-items:center;justify-content:space-between;font-size:15px;font-weight:700;color:var(--navy-deep)}
.faq-a{font-size:13px;line-height:1.55;color:var(--muted);padding-bottom:14px;margin-top:-4px}
.chev{width:9px;height:9px;border-right:2px solid #555;border-bottom:2px solid #555;transform:rotate(45deg) translateY(-3px)}
.chev.up{transform:rotate(-135deg) translateY(-2px)}
.faq-photo{left:598px;top:1810px;width:522px;height:413px;background:linear-gradient(180deg,#c98c3e 0%,#a96a2c 55%,#3d2715 85%,#221510 100%)}

/* Footer */
.site-footer{left:0;top:2288px;width:1200px;height:460px;background:linear-gradient(100deg,#1b3a85 0%,#0f2d73 50%,#13327a 100%);color:var(--white)}
.footer-brand{left:530px;top:2354px}
.footer-col h4{font-size:15px;font-weight:700;text-transform:uppercase;margin-bottom:24px}
.footer-col p{font-size:12.5px;font-weight:600;line-height:1.55}
.footer-col ul{list-style:none;font-size:13px;font-weight:700;line-height:1.35}
.seal{border-radius:4px;background:#e8ecf2}
.footer-call{left:778px;top:2460px;width:380px;height:150px;border:2px solid var(--white);border-radius:10px;padding:0 24px}
.copyright{left:0;top:2748px;width:1200px;height:38px;background:var(--white);text-align:center;line-height:38px;font-size:12.5px;font-weight:700;color:#333}
</style>
</head>
<body>

<header class="abs site-header">
  <div class="abs brand"><span class="brand-dot"></span>HULLS FOR HEROES</div>
  <div class="abs call-box header-call">
    <div class="ring">
      <svg width="34" height="34" viewBox="0 0 24 24"><path fill="#fff" d="M6.6 10.8a15.1 15.1 0 0 0 6.6 6.6l2.2-2.2a1 1 0 0 1 1-.25 11.4 11.4 0 0 0 3.6.57 1 1 0 0 1 1 1V20a1 1 0 0 1-1 1A17 17 0 0 1 3 4a1 1 0 0 1 1-1h3.5a1 1 0 0 1 1 1c0 1.25.2 2.45.57 3.57a1 1 0 0 1-.25 1z"/></svg>
    </div>
    <div>
      <div class="label">CALL TODAY TO DONATE</div>
      <div class="number">1-800-555-0147</div>
      <div class="note">Live Operators Available - 7 Days A Week</div>
    </div>
  </div>
</header>

<nav class="abs main-nav">
  <a style="left:176px" href="#how">HOW TO DONATE</a>
  <a style="left:366px" href="#why">WHY DONATE</a>
  <a style="left:526px" href="#faq">FAQ</a>
  <a style="left:609px" href="#about">ABOUT</a>
</nav>

<div class="abs hero-photo" role="img" aria-label="Photo of a uniformed soldier hugging a smiling young girl holding a small flag, with a motor yacht and city skyline behind"></div>

<form class="abs donate-form">
  <div class="form-icon"></div>
  <h2>DONATE YOUR BOATS ONLINE</h2>
  <div class="sub">Full Tax Deduction - Running or Not</div>
  <div class="fields">
    <div class="field">First Name</div>
    <div class="field">Last Name</div>
    <div class="field">Daytime Phone</div>
    <div class="field">Email</div>
    <div class="field wide">Pickup Address</div>
    <div class="field wide">Pickup City</div>
    <div class="field">Pickup State <span class="caret"></span></div>
    <div class="field">Zip Code</div>
    <div class="field">Choose Year <span class="caret"></span></div>
    <div class="field">Choose Make <span class="caret"></span></div>
    <div class="field wide">Vehicle Model</div>
  </div>
  <div class="btn-donate">DONATE NOW</div>
</form>

<section class="abs benefit-band" aria-label="Benefits"></section>
<svg class="abs band-badge" viewBox="0 0 520 226"><polygon points="0,22 430,22 520,113 430,204 0,204" fill="#a3120f"/><polygon points="0,204 430,204 410,226 0,226" fill="#6d0b09"/></svg>
<div class="abs band-badge-text">
  <div class="l1">DONATE YOUR BOATS TO</div>
  <div class="l2">VETERANS</div>
  <div class="l3">MAKE A DIFFERENCE</div>
</div>

<div class="abs perk" style="left:567px">
  <svg width="56" height="56" viewBox="0 0 56 56"><circle cx="28" cy="28" r="24" fill="none" stroke="#fff" stroke-width="4"/><path d="M17 29l8 8 15-17" fill="none" stroke="#fff" stroke-width="5"/></svg>
  You have<br>no costs</div>
<div class="abs perk" style="left:715px">
  <svg width="64" height="56" viewBox="0 0 64 56"><path d="M4 34h56l-8 12H12z" fill="#fff"/><path d="M18 33l6-12h18l8 12z" fill="#fff"/></svg>
  Free pickup,<br>running or not</div>
<div class="abs perk" style="left:863px">
  <svg width="48" height="56" viewBox="0 0 48 56"><rect x="6" y="3" width="36" height="50" fill="none" stroke="#fff" stroke-width="3"/><text x="24" y="30" fill="#fff" font-size="18" font-weight="700" text-anchor="middle" font-family="Open Sans,sans-serif">$</text><path d="M13 40h22M13 46h22" stroke="#fff" stroke-width="2"/></svg>
  We issue you an<br>IRS tax receipt</div>
<div class="abs perk" style="left:1008px">
  <svg width="52" height="56" viewBox="0 0 52 56"><rect x="14" y="3" width="32" height="44" fill="none" stroke="#fff" stroke-width="3"/><circle cx="16" cy="38" r="12" fill="#1e3c86" stroke="#fff" stroke-width="3"/><path d="M16 32v8M16 43v1" stroke="#fff" stroke-width="3"/><path d="M24 14h16M24 21h16" stroke="#fff" stroke-width="2"/></svg>
  We take care of<br>all paperwork.</div>

<h2 class="abs section-title" id="how" style="top:976px">HOW TO <em>DONATE</em></h2>

<div class="abs step" style="left:74px">
  <svg class="icon" width="70" height="100" viewBox="0 0 70 100"><rect x="4" y="4" width="16" height="12" fill="#0d2a6b"/><rect x="26" y="4" width="40" height="12" fill="#0d2a6b"/><rect x="4" y="24" width="62" height="12" fill="#0d2a6b"/><rect x="4" y="44" width="16" height="12" fill="#0d2a6b"/><rect x="26" y="44" width="40" height="12" fill="#0d2a6b"/><circle cx="18" cy="70" r="10" fill="#0d2a6b"/><path d="M12 78l-6 18 12-6 12 6-6-18" fill="#0d2a6b"/></svg>
  <div><h3>Call us at 1-800-555-0147 or<br>fill out the online form</h3><p>Donating your boat is easy and donation is accepted nationwide.</p></div>
</div>
<div class="abs step" style="left:446px">
  <svg class="icon" width="70" height="60" viewBox="0 0 70 60"><path d="M2 30h66l-10 18H12z" fill="#a3120f"/><path d="M20 29l8-14h20l8 14z" fill="#a3120f"/><rect x="30" y="19" width="5" height="6" fill="#fff"/><rect x="39" y="19" width="5" height="6" fill="#fff"/></svg>
  <div><h3>We pick up the boat</h3><p>Any boats is accepted and we will arrange to pick up your boat when it is most convenient for you.</p></div>
</div>
<div class="abs step" style="left:845px">
  <svg class="icon" width="70" height="80" viewBox="0 0 70 80"><rect x="14" y="4" width="50" height="64" fill="none" stroke="#0d2a6b" stroke-width="3"/><rect x="6" y="12" width="50" height="64" fill="#fff" stroke="#0d2a6b" stroke-width="3"/><text x="31" y="40" fill="#0d2a6b" font-size="20" font-weight="700" text-anchor="middle" font-family="Open Sans,sans-serif">$</text><rect x="16" y="50" width="30" height="16" fill="none" stroke="#0d2a6b" stroke-width="2"/></svg>
  <div><h3>Tax write-off</h3><p>Once the boat donation is complete, you will receive your tax deductable boat donation receipt.</p></div>
</div>

<div class="abs why-band" role="img" aria-label="Faded photo of a soldier saluting among rows of small flags"></div>
<h2 class="abs section-title" id="why" style="top:1314px">WHY DONATE <em>YOUR BOATS TO US</em></h2>

<div class="abs reason" style="left:56px;top:1393px">
  <div class="disc navy"><svg width="26" height="26"><rect x="3" y="3" width="20" height="20" fill="#fff"/></svg></div>
  <p><b>Trust Council A+ Rated &amp; IRS 501(c)3 Approved :</b> Free 24/7 Pickup with No DMV Hassles.</p>
</div>
<div class="abs reason" style="left:436px;top:1393px">
  <div class="disc red"><svg width="36" height="24" viewBox="0 0 36 24"><path d="M1 12h34l-6 10H7z" fill="none" stroke="#fff" stroke-width="2"/><path d="M10 11l4-8h10l4 8" fill="none" stroke="#fff" stroke-width="2"/></svg></div>
  <p><b>Free Local Towing :</b> We will pick up your boat donation, running or not, when it's most convenient.</p>
</div>
<div class="abs reason" style="left:817px;top:1393px">
  <div class="disc navy"><svg width="30" height="34" viewBox="0 0 30 34"><rect x="4" y="2" width="22" height="20" fill="none" stroke="#fff" stroke-width="2"/><circle cx="9" cy="28" r="4" fill="none" stroke="#fff" stroke-width="2"/><circle cx="21" cy="28" r="4" fill="none" stroke="#fff" stroke-width="2"/></svg></div>
  <p><b>Income Tax Deduction :</b> We issue you an IRS tax receipt &amp; offer the largest resale network to get you the highest tax write-off possible.</p>
</div>
<div class="abs reason" style="left:56px;top:1523px">
  <div class="disc red"><svg width="30" height="30" viewBox="0 0 30 30"><path d="M15 3l12 8-12 8-12-8z" fill="none" stroke="#fff" stroke-width="2"/><path d="M3 17l12 8 12-8" fill="none" stroke="#fff" stroke-width="2"/></svg></div>
  <p><b>No Paperwork Hassles :</b> We take any boat and handle everything: DMV, Smog and IRS paperwork.</p>
</div>
<div class="abs reason" style="left:436px;top:1523px">
  <div class="disc navy"><svg width="32" height="30" viewBox="0 0 32 30"><path d="M16 27C4 18 2 12 2 9a7 7 0 0 1 14-2 7 7 0 0 1 14 2c0 3-2 9-14 18z" fill="none" stroke="#fff" stroke-width="2"/><text x="16" y="19" fill="#fff" font-size="11" font-weight="700" text-anchor="middle" font-family="Open Sans,sans-serif">$</text></svg></div>
  <p><b>Boat donations help fund programs :</b> And benefit Veterans Aid Trust. An IRS 501(c)3 nonprofit organization.</p>
</div>
<div class="abs reason" style="left:817px;top:1523px">
  <div class="disc red"><svg width="28" height="28" viewBox="0 0 24 24"><path fill="#fff" d="M6.6 10.8a15.1 15.1 0 0 0 6.6 6.6l2.2-2.2a1 1 0 0 1 1-.25 11.4 11.4 0 0 0 3.6.57 1 1 0 0 1 1 1V20a1 1 0 0 1-1 1A17 17 0 0 1 3 4a1 1 0 0 1 1-1h3.5a1 1 0 0 1 1 1c0 1.25.2 2.45.57 3.57a1 1 0 0 1-.25 1z"/></svg></div>
  <p><b>Schedule a Free Pickup :</b> Complete the form and a representative will call you to arrange a convenient time to pickup your boat.</p>
</div>

<h2 class="abs section-title" id="faq" style="top:1732px">FREQUENTLY ASKED <em>QUESTIONS</em></h2>

<div class="abs faq">
  <div class="faq-item"><div class="faq-q">What types of boats can be donated? <span class="chev"></span></div></div>
  <div class="faq-item"><div class="faq-q">What paperwork do I need to donate my boat? <span class="chev up"></span></div>
    <div class="faq-a">All you need is a title, free of all liens. We will request some general information from you at the time of donation such as, the year, make, and model of the boat, as well as its general mechanical condition. We accept all boats, running or non-running.</div></div>
  <div class="faq-item"><div class="faq-q">Is my donated boat tax -deductible? <span class="chev"></span></div></div>
  <div class="faq-item"><div class="faq-q">What if the boat is not registered in my name? <span class="chev"></span></div></div>
  <div class="faq-item"><div class="faq-q">How much will I receive as a tax deduction for my boat? <span class="chev"></span></div></div>
  <div class="faq-item"><div class="faq-q">When will I receive my tax receipt? <span class="chev"></span></div></div>
  <div class="faq-item"><div class="faq-q">How do I schedule a pick up? <span class="chev"></span></div></div>
</div>
<div class="abs faq-photo" role="img" aria-label="Silhouettes of soldiers raising a flag against a golden sunset sky"></div>

<footer class="abs site-footer" id="about"></footer>
<div class="abs brand footer-brand" style="top:2352px;left:530px"><span class="brand-dot"></span>HULLS FOR HEROES</div>

<div class="abs footer-col" style="left:72px;top:2462px;width:250px;color:#fff">
  <h4>About Hulls for Heroes</h4>
  <p>Hulls for Heroes turns donated boats into support for veterans and their families. We handle towing, titles and tax paperwork so giving is simple, fast and free for every donor across the country.</p>
</div>
<div class="abs footer-col" style="left:380px;top:2462px;color:#fff">
  <h4>Navigation</h4>
  <ul><li>HOW TO DONATE</li><li>WHY DONATE</li><li>FAQ</li><li>ABOUT</li></ul>
</div>
<div class="abs footer-col" style="left:556px;top:2462px;color:#fff">
  <h4>Safe &amp; Secure</h4>
  <div class="seal" style="width:156px;height:52px"></div>
  <div class="seal" style="width:114px;height:40px;margin-top:12px"></div>
  <div style="width:48px;height:48px;border-radius:50%;background:#e8ecf2;margin-top:12px"></div>
</div>
<div class="abs call-box footer-call">
  <div class="ring">
    <svg width="34" height="34" viewBox="0 0 24 24"><path fill="#fff" d="M6.6 10.8a15.1 15.1 0 0 0 6.6 6.6l2.2-2.2a1 1 0 0 1 1-.25 11.4 11.4 0 0 0 3.6.57 1 1 0 0 1 1 1V20a1 1 0 0 1-1 1A17 17 0 0 1 3 4a1 1 0 0 1 1-1h3.5a1 1 0 0 1 1 1c0 1.25.2 2.45.57 3.57a1 1 0 0 1-.25 1z"/></svg>
  </div>
  <div>
    <div class="label">CALL TODAY TO DONATE</div>
    <div class="number">1-800-555-0147</div>
    <div class="note">Live Operators Available - 7 Days A Week</div>
  </div>
</div>

<div class="abs copyright">COPYRIGHT © 2017 HULLS FOR HEROES. PRIVACY POLICY | TERMS &amp; CONDITIONS. ALL RIGHTS RESERVED.</div>

</body>
</html>
```